Business cards for Harbourline Supply Pty Ltd that import building products into Australia from China
Target Market(s)
Business to Business
Industry/Entity Type
Business
Contact Information for Business Card
Front: Logo and Business Name
Rear:
Desmond Varrick
General Manager
Mobile: 0427 561 394
email: dessie@harbourlinesupply.com.au
alternative email: dessie@outbackworks.com.au
web: www.harbourlinesupply.com.au
Kestrel Bay, Marlow and Tindara
Colors
ec1f27
fbee3d

```html
<!DOCTYPE html>
<html lang="en">
<head>
<meta charset="utf-8">
<title>Harbourline Supply Pty Ltd – Business Cards</title>
<link rel="stylesheet" href="https://fonts.googleapis.com/css2?family=Open+Sans:wght@400;600;700&display=swap">
<style>
  :root {
    --brand-red: #ec1f27;
    --brand-yellow: #fbee3d;
    --ink: #1d1d1b;
    --paper: #ffffff;
    --backdrop: #545454;
  }
  * { margin: 0; padding: 0; box-sizing: border-box; }
  html, body { width: 1200px; height: 900px; overflow: hidden; }
  body {
    background: var(--backdrop);
    font-family: "Open Sans", Arial, sans-serif;
    color: var(--ink);
    position: relative;
  }
  .card {
    position: absolute;
    top: 306px;
    width: 440px;
    height: 271px;
    border-radius: 10px;
    overflow: hidden;
  }
  .card--contact { left: 149px; background: var(--paper); }
  .card--brand { left: 608px; background: var(--brand-red); }

  .accent { position: absolute; left: 0; top: 26px; }

  .person { position: absolute; left: 34px; top: 29px; }
  .person__name { font-size: 16px; font-weight: 600; line-height: 20px; letter-spacing: 0.1px; }
  .person__surname { color: var(--brand-red); }
  .person__role { font-size: 12px; line-height: 15px; }

  .brand-lockup {
    position: absolute;
    left: 200px;
    top: 40px;
    width: 215px;
    display: flex;
    flex-direction: column;
    align-items: center;
    gap: 14px;
  }
  .brand-lockup__square { width: 44px; height: 44px; background: var(--brand-red); }
  .brand-lockup__name {
    font-size: 21px;
    font-weight: 700;
    line-height: 25px;
    text-align: center;
    color: var(--ink);
  }

  .contacts { position: absolute; left: 26px; top: 170px; list-style: none; }
  .contacts li {
    display: flex;
    align-items: center;
    gap: 6px;
    font-size: 12px;
    line-height: 16px;
    white-space: nowrap;
  }
  .contacts svg { width: 11px; height: 11px; flex: none; }

  .locations {
    position: absolute;
    right: 26px;
    top: 214px;
    font-size: 12px;
    line-height: 16px;
    white-space: nowrap;
  }

  .base-band { position: absolute; left: 0; bottom: 0; }

  .brand-pattern {
    position: absolute;
    inset: 0;
    background: var(--brand-red);
  }
  .brand-mark {
    position: absolute;
    inset: 0;
    display: flex;
    align-items: center;
    justify-content: center;
    gap: 12px;
  }
  .brand-mark__square { width: 34px; height: 34px; background: var(--brand-yellow); }
  .brand-mark__name {
    font-size: 24px;
    font-weight: 700;
    color: var(--paper);
    line-height: 28px;
  }
</style>
</head>
<body>
  <section class="card card--contact" aria-label="Business card, contact side">
    <svg class="accent" width="30" height="36" viewBox="0 0 30 36" aria-hidden="true">
      <polygon points="0,0 12,0 16,36 0,36" fill="var(--brand-red)"/>
      <polygon points="12,0 28,0 29,36 16,36" fill="var(--brand-yellow)"/>
    </svg>

    <div class="person">
      <p class="person__name">DESMOND <span class="person__surname">VARRICK</span></p>
      <p class="person__role">General Manager</p>
    </div>

    <div class="brand-lockup">
      <span class="brand-lockup__square"></span>
      <p class="brand-lockup__name">Harbourline Supply<br>Pty Ltd</p>
    </div>

    <ul class="contacts">
      <li>
        <svg viewBox="0 0 11 11" aria-hidden="true"><rect x="2.5" y="0.5" width="6" height="10" rx="1.2" fill="none" stroke="var(--brand-red)" stroke-width="1.4"/></svg>
        0427 561 394
      </li>
      <li>
        <svg viewBox="0 0 11 11" aria-hidden="true"><rect x="0.5" y="2" width="10" height="7" fill="var(--brand-red)"/><polyline points="0.5,2.5 5.5,6 10.5,2.5" fill="none" stroke="#fff" stroke-width="1"/></svg>
        dessie@harbourlinesupply.com.au
      </li>
      <li>
        <svg viewBox="0 0 11 11" aria-hidden="true"><rect x="0.5" y="2" width="10" height="7" fill="var(--brand-red)"/><polyline points="0.5,2.5 5.5,6 10.5,2.5" fill="none" stroke="#fff" stroke-width="1"/></svg>
        dessie@outbackworks.com.au
      </li>
      <li>
        <svg viewBox="0 0 11 11" aria-hidden="true"><circle cx="5.5" cy="5.5" r="4.8" fill="var(--brand-red)"/></svg>
        www.harbourlinesupply.com.au
      </li>
    </ul>

    <p class="locations">Kestrel Bay, Marlow and Tindara</p>

    <svg class="base-band" width="440" height="22" viewBox="0 0 440 22" aria-hidden="true">
      <polygon points="0,8 218,8 210,22 0,22" fill="var(--brand-red)"/>
      <polygon points="222,2 440,2 440,22 208,22" fill="var(--brand-yellow)"/>
    </svg>
  </section>

  <section class="card card--brand" aria-label="Business card, brand side">
    <div class="brand-pattern" role="img" aria-label="Faint repeating brand pattern on red"></div>
    <div class="brand-mark">
      <span class="brand-mark__square"></span>
      <p class="brand-mark__name">Harbourline Supply</p>
    </div>
  </section>
</body>
</html>
```